Business Card Design

We provide services doing multiple jobs in the construction industry.Please note: The company name needs to be ROCK SOLID BUILDING SERVICESAttached logo was an example of what we wanted. Can you change up the colors?

Industry/Entity Type

Construction

Contact Information for Business Card

ROCK SOLID BUILDING SERVICES5401 HUDSON BEND RDAUSTIN, TX 78734(512)243-6854ROCKSOLIDBUILDINGSERVICES@GMAIL.COM

```html
<!DOCTYPE html>
<html lang="en">
<head>
<meta charset="utf-8">
<title>Pearlwood Framing Works – Business Card</title>
<link rel="stylesheet" href="https://fonts.googleapis.com/css2?family=Exo+2:wght@600&family=Alegreya+Sans:wght@500&display=swap">
<style>
  :root {
    --page-bg: #6f93b3;
    --card-bg: #2b2870;
    --band-top: #2a2766;
    --band-bottom: #15133a;
    --rule: #8e8bbf;
    --cream: #ecdfc6;
  }
  html, body {
    margin: 0;
    width: 1200px;
    height: 902px;
    overflow: hidden;
    background: var(--page-bg);
  }
  .card {
    position: absolute;
    left: 100px;
    top: 165px;
    width: 1000px;
    height: 571px;
    background: var(--card-bg);
    color: var(--cream);
  }
  .brand-mark {
    position: absolute;
    left: 0;
    right: 0;
    top: 112px;
    display: flex;
    justify-content: center;
    align-items: center;
    gap: 16px;
    font-family: "Exo 2", sans-serif;
    font-weight: 600;
    font-size: 40px;
    letter-spacing: 1px;
  }
  .brand-mark .dot {
    width: 18px;
    height: 18px;
    background: var(--cream);
  }
  .name-band {
    position: absolute;
    left: 0;
    right: 0;
    top: 271px;
    height: 103px;
    background: linear-gradient(var(--band-top), var(--band-bottom));
    border-top: 2px solid var(--rule);
    border-bottom: 3px solid #0d0c26;
    display: flex;
    align-items: center;
    justify-content: center;
    box-sizing: border-box;
  }
  .company-name {
    margin: 0;
    font-family: "Exo 2", sans-serif;
    font-weight: 600;
    font-size: 48px;
    letter-spacing: 1px;
  }
  .contact {
    position: absolute;
    left: 0;
    right: 0;
    top: 394px;
    text-align: center;
    font-family: "Alegreya Sans", sans-serif;
    font-weight: 500;
    font-size: 26px;
    line-height: 38px;
  }
  .contact p { margin: 0; }
  .bottom-rule {
    position: absolute;
    left: 0;
    right: 0;
    top: 517px;
    height: 2px;
    background: var(--rule);
  }
  .bottom-strip {
    position: absolute;
    left: 0;
    right: 0;
    top: 519px;
    bottom: 0;
    background: linear-gradient(var(--band-top), #1d1b4c);
  }
</style>
</head>
<body>
  <div class="card">
    <div class="brand-mark"><span class="dot"></span>PEARLWOOD FRAMING</div>
    <div class="name-band">
      <h1 class="company-name">PEARLWOOD FRAMING WORKS</h1>
    </div>
    <div class="contact">
      <p class="phone">(512)555-0193</p>
      <p class="email">Pearlwoodframingworks@mailnest.example</p>
      <p class="address">7732 Fernglen Pass LN Austin, TX 78734</p>
    </div>
    <div class="bottom-rule"></div>
    <div class="bottom-strip"></div>
  </div>
</body>
</html>
```